Power Point Template

I would like to have a power point template for our company.
See our website: www.brekkavikfjord.se for logo/colors and inspiration.

The template will be used for bank meetings etc, so it should be formal and professional.

Should show examples of various layouts.
Updates

I want the following headings/sections/example slides: - Slide with table of contents - Slide with bullets (just to show how a bullet list looks like) - Slide with project timeline - Slide with business case calculations (table e.g.) - slide with pictures with room for descriptive text (to show inspirational pictures, one slide per section: exterior, interior upper floor, exterior lower floor)? - Slide where our buildings are described (bullet list) - Slide with presentation of our business partners - First page with a faded background picture of our building (the one where our logo is shown)

Industry/Entity Type

It Company

```html
<!DOCTYPE html>
<html lang="en">
<head>
<meta charset="utf-8">
<title>Our Features – brekkavikfjord</title>
<link href="https://fonts.googleapis.com/css2?family=Roboto+Condensed:wght@400&display=swap" rel="stylesheet">
<style>
  :root {
    --navy: #1d304c;
    --navy-deep: #142238;
    --navy-ring: #1b2c45;
    --accent: #fbb03b;
    --accent-text: #f9a62b;
    --white: #ffffff;
    --ink: #111111;
  }
  * { margin: 0; padding: 0; box-sizing: border-box; }
  html, body { width: 1200px; height: 900px; overflow: hidden; }
  body { font-family: "Roboto Condensed", "Arial Narrow", sans-serif; background: var(--white); }

  .slide { position: relative; width: 1200px; height: 900px; overflow: hidden; background: var(--accent); }

  .hero-backdrop {
    position: absolute; left: 0; top: 0; width: 1200px; height: 627px;
    background:
      linear-gradient(180deg, rgba(29,48,76,0.92) 0%, rgba(33,54,84,0.88) 55%, rgba(27,44,69,0.95) 100%),
      linear-gradient(100deg, #5b6f88 0%, #3b5170 45%, #2a3f5d 100%);
  }

  .slide-title {
    position: absolute; left: 21px; top: 18px;
    font-size: 36px; font-weight: 400; color: var(--white); letter-spacing: 0.5px;
  }
  .title-rule { position: absolute; left: 0; top: 66px; width: 255px; height: 3px; background: var(--accent); }

  .brand { position: absolute; right: 24px; top: 34px; display: flex; align-items: center; gap: 10px; }
  .brand-square { width: 22px; height: 22px; background: var(--white); }
  .brand-name { font-size: 26px; color: var(--white); font-weight: 400; }

  .feature { position: absolute; left: 57px; width: 1090px; }
  .feature-one { top: 114px; }
  .feature-two { top: 310px; }
  .feature-heading { font-size: 25px; color: var(--accent-text); font-weight: 400; line-height: 36px; }
  .feature-text { font-size: 20.5px; line-height: 33px; color: var(--white); margin-top: 3px; }

  .gallery { position: absolute; left: 0; top: 524px; width: 1200px; height: 216px; }
  .gallery-item { position: absolute; top: 0; width: 216px; height: 216px; }
  .gallery-item svg { display: block; }

  .summary-text {
    position: absolute; left: 57px; top: 768px; width: 1090px;
    font-size: 20.5px; line-height: 33px; color: var(--ink);
  }
</style>
</head>
<body>
<main class="slide">
  <div class="hero-backdrop" role="img" aria-label="Faded photograph of the company's office building facade under an overcast sky"></div>

  <h1 class="slide-title">OUR FEATURES</h1>
  <div class="title-rule"></div>

  <div class="brand">
    <span class="brand-square"></span>
    <span class="brand-name">brekkavikfjord</span>
  </div>

  <section class="feature feature-one">
    <h2 class="feature-heading">Subtext here</h2>
    <p class="feature-text">Lorem Ipsum is simply dummy text of the printing and typesetting industry. Lorem Ipsum has been the industry's standard dummy text ever since the 1500s, when an unknown printer took a galley of type and scrambled it to make a type specimen book. It has survived not only five centuries, but also the leap into electronic typesetting.</p>
  </section>

  <section class="feature feature-two">
    <h2 class="feature-heading">Subtext here</h2>
    <p class="feature-text">Lorem Ipsum is simply dummy text of the printing and typesetting industry. Lorem Ipsum has been the industry's standard dummy text ever since the 1500s, when an unknown printer took a galley of type and scrambled it to make a type specimen book. It has survived not only five centuries, but also the leap into electronic typesetting.</p>
  </section>

  <div class="gallery">
    <figure class="gallery-item" style="left:12px">
      <svg width="216" height="216" viewBox="0 0 216 216" role="img" aria-label="Photo of a grey building wall with a row of windows">
        <defs><linearGradient id="g1" x1="0" y1="0" x2="1" y2="1"><stop offset="0" stop-color="#b9c6d2"/><stop offset="1" stop-color="#7f8d99"/></linearGradient></defs>
        <circle cx="108" cy="108" r="108" fill="var(--navy-ring)"/>
        <circle cx="108" cy="108" r="99" fill="#ffffff"/>
        <circle cx="108" cy="108" r="94" fill="url(#g1)"/>
      </svg>
    </figure>
    <figure class="gallery-item" style="left:252px">
      <svg width="216" height="216" viewBox="0 0 216 216" role="img" aria-label="Photo of the building corner with windows and a tree">
        <defs><linearGradient id="g2" x1="0" y1="0" x2="1" y2="1"><stop offset="0" stop-color="#c3ced8"/><stop offset="1" stop-color="#86939f"/></linearGradient></defs>
        <circle cx="108" cy="108" r="108" fill="var(--navy-ring)"/>
        <circle cx="108" cy="108" r="99" fill="#ffffff"/>
        <circle cx="108" cy="108" r="94" fill="url(#g2)"/>
      </svg>
    </figure>
    <figure class="gallery-item" style="left:492px">
      <svg width="216" height="216" viewBox="0 0 216 216" role="img" aria-label="Close-up photo of facade windows">
        <defs><linearGradient id="g3" x1="0" y1="0" x2="1" y2="1"><stop offset="0" stop-color="#cbd7e0"/><stop offset="1" stop-color="#93a6b4"/></linearGradient></defs>
        <circle cx="108" cy="108" r="108" fill="var(--navy-ring)"/>
        <circle cx="108" cy="108" r="99" fill="#ffffff"/>
        <circle cx="108" cy="108" r="94" fill="url(#g3)"/>
      </svg>
    </figure>
    <figure class="gallery-item" style="left:732px">
      <svg width="216" height="216" viewBox="0 0 216 216" role="img" aria-label="Photo of a red truck parked at the loading area">
        <defs><linearGradient id="g4" x1="0" y1="0" x2="0" y2="1"><stop offset="0" stop-color="#c9473f"/><stop offset="1" stop-color="#6d5a55"/></linearGradient></defs>
        <circle cx="108" cy="108" r="108" fill="var(--navy-ring)"/>
        <circle cx="108" cy="108" r="99" fill="#ffffff"/>
        <circle cx="108" cy="108" r="94" fill="url(#g4)"/>
      </svg>
    </figure>
    <figure class="gallery-item" style="left:972px">
      <svg width="216" height="216" viewBox="0 0 216 216" role="img" aria-label="Photo of the building wall carrying the company sign">
        <defs><linearGradient id="g5" x1="0" y1="0" x2="1" y2="1"><stop offset="0" stop-color="#d3dbe2"/><stop offset="1" stop-color="#9aa7b2"/></linearGradient></defs>
        <circle cx="108" cy="108" r="108" fill="var(--navy-ring)"/>
        <circle cx="108" cy="108" r="99" fill="#ffffff"/>
        <circle cx="108" cy="108" r="94" fill="url(#g5)"/>
      </svg>
    </figure>
  </div>

  <p class="summary-text">Lorem Ipsum is simply dummy text of the printing and typesetting industry. Lorem Ipsum has been the industry's standard dummy text ever since the 1500s, when an unknown printer took a galley of type and scrambled it to make a type specimen book. It has survived not only five centuries, but also the leap into electronic typesetting.</p>
</main>
</body>
</html>
```